Email design required

We need a design for a paid B2B email campaign and facebook / retargeting banner ads that match the same style.

Website: http://pelmora.staging.hostvantry.com/
Campaign Name: KEX Weariness
Example: http://liftmarrowsites.com/kex-weariness/
- I made this over the weekend. It has the right words, but the style / layout needs to change

Size: 600 pixels wide, no limit on length

Formatting:
Format CSS inline only - This will ensure that size, font family, colour, line height, etc. will all remain the same once it is dropped into our newsletter sending software. See below as an

example,

Here's a mockup of

Target Market(s)

Canadian mortgage brokers

Industry/Entity Type

Campaign

Font styles to use
Sans Serif

Colors
3277b5

Requirements
Must have
• Text from my website example http://liftmarrowsites.com/kex-weariness/
• Otherwise, do whatever you think would look good.

```html
<!DOCTYPE html>
<html lang="en">
<head>
<meta charset="utf-8">
<title>Pelmora – KEX Weariness</title>
<link href="https://fonts.googleapis.com/css2?family=Open+Sans:ital,wght@0,400;0,600;0,700;1,400&display=swap" rel="stylesheet">
<style>
  :root {
    --stage: #2a2a2a;
    --paper: #ffffff;
    --header-bg: #f7f7f7;
    --navy: #22345a;
    --brand-blue: #3277b5;
    --orange: #f7941d;
    --ink: #333333;
    --muted: #777777;
    --row-grey: #eef0f4;
    --row-green: #e6fde0;
    --about-bg: #eeeeee;
    --footer-bg: #3d3a4e;
    --avatar: #555555;
  }
  * { box-sizing: border-box; margin: 0; padding: 0; }
  html, body { width: 960px; height: 1200px; overflow: hidden; }
  body {
    background: var(--stage);
    font-family: "Open Sans", Arial, sans-serif;
    color: var(--ink);
    position: relative;
  }
  .email {
    position: absolute;
    left: 240px;
    top: 117px;
    width: 480px;
    background: var(--paper);
  }

  /* header */
  .top-bar {
    height: 59px;
    background: var(--header-bg);
    display: flex;
    align-items: center;
    justify-content: space-between;
    padding: 0 29px 0 21px;
  }
  .brand {
    display: flex;
    align-items: center;
    gap: 5px;
    color: var(--brand-blue);
    font-weight: 600;
    font-size: 20px;
    letter-spacing: -0.2px;
  }
  .brand-square { width: 15px; height: 15px; background: var(--brand-blue); }
  .top-link { font-size: 11px; color: #666; }

  /* hero */
  .hero {
    height: 206px;
    background: var(--navy);
    position: relative;
    color: #fff;
  }
  .hero-title {
    position: absolute;
    top: 6px;
    left: 0; right: 0;
    text-align: center;
    font-size: 29px;
    font-weight: 700;
  }
  .hero-offer {
    position: absolute;
    left: 24px;
    top: 80px;
    width: 240px;
    text-align: center;
    font-size: 11.5px;
    line-height: 16px;
    font-weight: 600;
  }
  .price { color: var(--orange); }
  .hero-btn {
    position: absolute;
    left: 58px;
    top: 130px;
    width: 144px;
    height: 34px;
    border-radius: 17px;
    background: var(--orange);
    color: #fff;
    font-size: 11.5px;
    font-weight: 700;
    display: flex; align-items: center; justify-content: center;
  }
  .hero-illustration {
    position: absolute;
    left: 274px;
    top: 64px;
    width: 146px;
    height: 119px;
    background: linear-gradient(180deg, #3a4c72, #2a3c62);
    border-radius: 4px;
  }

  /* section bars */
  .section-bar {
    background: var(--brand-blue);
    color: #fff;
    text-align: center;
    font-weight: 700;
    font-size: 13px;
    height: 38px;
    line-height: 38px;
  }

  /* review */
  .review {
    height: 135px;
    position: relative;
  }
  .avatar {
    position: absolute;
    left: 47px;
    top: 14px;
    width: 100px; height: 100px;
    border-radius: 50%;
    background: var(--avatar);
  }
  .review-text {
    position: absolute;
    left: 198px;
    top: 23px;
    width: 256px;
    font-style: italic;
    font-size: 10px;
    line-height: 16px;
    color: var(--muted);
  }
  .review-author {
    margin-top: 6px;
    font-style: normal;
    font-weight: 600;
    font-size: 10px;
    color: #666;
  }

  /* compare */
  .compare { padding: 21px 0 0; height: 178px; border-bottom: 1px solid #eee; }
  .compare-head {
    display: flex;
    align-items: center;
    height: 36px;
    margin-left: 190px;
  }
  .compare-head .brand { width: 128px; font-size: 17px; justify-content: center; }
  .other-guys { width: 130px; text-align: center; font-size: 11.5px; font-weight: 700; color: #111; padding-top: 4px; }
  .compare-table {
    width: 403px;
    margin: 16px auto 0;
    border-collapse: collapse;
    font-size: 10px;
  }
  .compare-table tr { height: 27px; }
  .compare-table tr:nth-child(odd) { background: var(--row-grey); }
  .compare-table tr:nth-child(even) { background: var(--row-green); }
  .compare-table .icon { width: 26px; padding-left: 4px; }
  .compare-table .icon svg { display: block; }
  .compare-table .label { width: 114px; color: #555; }
  .compare-table .ours { width: 130px; text-align: center; font-weight: 700; color: #222; }
  .compare-table .theirs { text-align: center; color: #666; }

  /* cta */
  .cta { height: 79px; display: flex; justify-content: center; padding-top: 3px; }
  .cta-btn {
    width: 255px; height: 60px;
    border-radius: 30px;
    background: var(--orange);
    color: #fff;
    text-align: center;
    padding-top: 8px;
  }
  .cta-main { font-size: 19px; font-weight: 700; letter-spacing: 0.6px; line-height: 24px; }
  .cta-sub { font-size: 10.5px; font-weight: 700; letter-spacing: 0.3px; }

  /* about */
  .about { display: flex; height: 192px; }
  .about-visual {
    width: 240px;
    background: linear-gradient(180deg, #3b5788, #2c4775);
    display: flex; align-items: center; justify-content: center;
    color: #fff;
    font-size: 32px;
    font-weight: 600;
    padding-top: 40px;
  }
  .about-copy { width: 240px; background: var(--about-bg); }
  .about-copy .section-bar { font-weight: 400; font-size: 13.5px; }
  .about-copy p {
    padding: 8px 20px 0 24px;
    font-size: 10px;
    line-height: 16px;
    color: #666;
  }

  /* footer */
  .footer {
    height: 38px;
    background: var(--footer-bg);
    color: #fff;
    font-size: 10px;
    display: flex; align-items: center; justify-content: space-between;
    padding: 0 26px 0 23px;
  }
</style>
</head>
<body>
  <main class="email">
    <header class="top-bar">
      <div class="brand"><span class="brand-square"></span>Pelmora</div>
      <span class="top-link">Contact</span>
    </header>

    <section class="hero">
      <h1 class="hero-title">Experiencing KEX Weariness?</h1>
      <p class="hero-offer">Unlimited Notice of Assessment Orders<br>For Just <span class="price">$29 / Month</span></p>
      <div class="hero-btn">Get Started Now</div>
      <div class="hero-illustration" role="img" aria-label="Illustration of a tired worker slumped over a desk"></div>
    </section>

    <div class="section-bar">Customer Reviews</div>
    <section class="review">
      <div class="avatar" role="img" aria-label="Customer portrait"></div>
      <blockquote class="review-text">
        I've used a few different services for this and Pelmora is by far the best. Fraction of the cost and I have the required docs within a couple of hours at most. Makes my life so much easier.
        <div class="review-author">Dario Velcourt, Hartline Calgary</div>
      </blockquote>
    </section>

    <div class="section-bar">Compare KEX Services</div>
    <section class="compare">
      <div class="compare-head">
        <div class="brand"><span class="brand-square"></span>Pelmora</div>
        <div class="other-guys">‘Other Guys’</div>
      </div>
      <table class="compare-table">
        <tr>
          <td class="icon"><svg width="11" height="11" viewBox="0 0 12 12"><circle cx="6" cy="6" r="5" fill="none" stroke="#555" stroke-width="1.4"/><path d="M3.5 6l2 2 4-4.5" fill="none" stroke="#555" stroke-width="1.6"/></svg></td>
          <td class="label">Price</td><td class="ours">$29 / month</td><td class="theirs">$39 / Order</td>
        </tr>
        <tr>
          <td class="icon"><svg width="11" height="11" viewBox="0 0 12 12"><circle cx="6" cy="6" r="5" fill="none" stroke="#555" stroke-width="1.4"/><path d="M3.5 6l2 2 4-4.5" fill="none" stroke="#555" stroke-width="1.6"/></svg></td>
          <td class="label">Units</td><td class="ours">Unlimited</td><td class="theirs">Just One</td>
        </tr>
        <tr>
          <td class="icon"><svg width="11" height="11" viewBox="0 0 12 12"><circle cx="6" cy="6" r="5" fill="none" stroke="#555" stroke-width="1.4"/><path d="M3.5 6l2 2 4-4.5" fill="none" stroke="#555" stroke-width="1.6"/></svg></td>
          <td class="label">Turnaround</td><td class="ours">4 Hours</td><td class="theirs">1 Day</td>
        </tr>
        <tr>
          <td class="icon"><svg width="11" height="11" viewBox="0 0 12 12"><circle cx="6" cy="6" r="5" fill="none" stroke="#555" stroke-width="1.4"/><path d="M3.5 6l2 2 4-4.5" fill="none" stroke="#555" stroke-width="1.6"/></svg></td>
          <td class="label">Other Services</td><td class="ours">Several</td><td class="theirs">X</td>
        </tr>
      </table>
    </section>

    <section class="cta">
      <div class="cta-btn">
        <div class="cta-main">GET STARTED NOW</div>
        <div class="cta-sub">30-Day Money Back Guarantee</div>
      </div>
    </section>

    <section class="about">
      <div class="about-visual" role="img" aria-label="Photo of blue office filing binders">Pelmora</div>
      <div class="about-copy">
        <div class="section-bar">About Us</div>
        <p>Pelmora provides on-demand administrative support for Mortgage Professionals across Canada. Everything from Notice of Assessment and Title Orders to inbound document sorting and lender fulfilment can be outsouced at a fraction of the cost of a full time administrator.</p>
      </div>
    </section>

    <footer class="footer">
      <span>© Pelmora 2016 All rights reserved.</span>
      <span>Unsubscribe here</span>
    </footer>
  </main>
</body>
</html>
```